UI/ UX Design for ERP Software

We need a new UX/UI interface for a ERP software for property managers. Our CMMS / ERP solution is made based on responsive design technologies and is coded in PHP.
The overall UX to be similar to Tev Ulna - easy navigation, intuitive menus.

Industry/Entity Type

Property Management

Number of Pages Required

5+ page

Requirements
Must have
• Round dock buttons
Consistent icons across the application
Enough Spacing between buttons/icons/ menu
Consistent Font
Nice to have
• We would like the UX to allow the users to use the application without /minimum training.
Should not have
• we don't want anything that is classic with respect to UX

```html
<!DOCTYPE html>
<html lang="en">
<head>
<meta charset="utf-8">
<title>Keystone · Dashboard</title>
<link href="https://fonts.googleapis.com/css2?family=Lato:wght@400;700&display=swap" rel="stylesheet">
<style>
:root{
  --brand:#0a78f0;
  --page:#edf3fc;
  --panel:#ffffff;
  --ink:#2b3440;
  --muted:#8a8f97;
  --grid:#e6e8ec;
  --line:#f45fb0;
  --online:#5ce28a;
  --search:#eef0f3;
}
*{box-sizing:border-box;margin:0;padding:0}
html,body{width:1156px;height:1200px;overflow:hidden;background:var(--page);font-family:"Lato",sans-serif;color:var(--ink)}
.stage{position:absolute;left:0;top:0;width:1400px;height:1453px;transform:scale(.8257);transform-origin:0 0;background:var(--page)}
.abs{position:absolute}

/* header */
.topbar{left:0;top:0;width:1400px;height:102px;background:#fff}
.brand{left:0;top:0;width:373px;height:102px;background:var(--brand);display:flex;align-items:center;justify-content:center;gap:14px;color:#fff;font-size:42px;font-weight:700}
.brand-mark{width:26px;height:26px;border-radius:50%;background:#fff}
.search{left:570px;top:21px;width:347px;height:59px;background:var(--search);display:flex;align-items:center;padding-left:22px;gap:10px;color:#9aa0a8;font-size:18px}
.icon-btn{top:28px}
.user{left:1092px;top:21px;display:flex;align-items:center;gap:14px;font-size:22px;color:#3a4b66}
.avatar-round{width:60px;height:60px;border-radius:50%;background:radial-gradient(circle at 50% 40%,#c79c82,#4b3b33 75%);border:2px solid #ddd}
.menu{left:1328px;top:40px}

/* page head */
.page-title{left:37px;top:128px;font-size:28px;color:#2e3b55}
.page-sub{left:39px;top:165px;font-size:17px;color:var(--muted)}
.range-label{left:984px;top:146px;font-size:18px;color:#5c6678}
.range-box{left:1094px;top:131px;width:265px;height:54px;background:#fff;display:flex;align-items:center;justify-content:space-between;padding:0 14px;font-size:15px;color:#444;letter-spacing:.3px}

/* stat cards */
.stat{top:216px;height:100px;display:flex;align-items:center;gap:14px;padding-left:26px;color:#fff}
.stat svg{flex:none}
.stat-label{font-size:17px;font-weight:700;letter-spacing:.2px}
.stat-value{font-size:23px;font-weight:700;margin-top:2px}
.c-props{left:22px;width:216px;background:linear-gradient(90deg,#ec6ad6,#f98bc1)}
.c-tenants{left:248px;width:216px;background:linear-gradient(90deg,#f99a5c,#fda03c)}
.c-area{left:473px;width:317px;background:linear-gradient(90deg,#9a4ef2,#c07bf7)}
.c-rented{left:800px;width:280px;background:linear-gradient(90deg,#22bfae,#40e39a)}
.c-vacant{left:1090px;width:280px;background:linear-gradient(90deg,#14a6f5,#0dc4fb)}

/* chart */
.chart-panel{left:27px;top:327px;width:1344px;height:591px;background:var(--panel)}
.filters{right:27px;top:18px;display:flex;gap:14px;font-size:17px;color:#555;font-weight:700}
.filters label{display:flex;align-items:center;gap:10px}
.radio{width:16px;height:16px;border-radius:50%;border:1.5px solid #c7cbd1;display:inline-block}
.radio.on{border:none;background:var(--brand);box-shadow:0 0 0 3px #d7e8fd}

/* bottom */
.donut-panel{left:32px;top:997px;width:673px;height:421px;background:var(--panel)}
.legend{left:340px;top:42px;list-style:none;font-size:17px;font-weight:700;color:#222}
.legend li{display:flex;align-items:center;gap:8px;height:50.6px}
.dot{width:15px;height:15px;border-radius:50%}
.users-title{left:749px;top:956px;font-size:24px;color:#222}
.users-range{left:1237px;top:961px;font-size:19px;color:#6a717c}
.users-panel{left:745px;top:997px;width:623px;height:421px;background:var(--panel)}
.user-row{left:25px;display:flex;align-items:center;width:572px}
.photo{width:81px;height:72px;border-radius:22px;flex:none}
.user-info{margin-left:21px;flex:1}
.user-name{font-size:24px;color:#222}
.user-role{font-size:17px;color:#6d737c;margin-top:4px}
.status{width:115px;height:40px;border-radius:10px;background:#fff;box-shadow:0 6px 20px rgba(0,0,0,.07);color:var(--online);font-size:21px;display:flex;align-items:center;justify-content:center}
</style>
</head>
<body>
<div class="stage">

  <header class="abs topbar">
    <div class="abs brand"><span class="brand-mark"></span>Keystone</div>
    <div class="abs search">
      <svg width="18" height="18" viewBox="0 0 18 18"><circle cx="7.5" cy="7.5" r="5.5" fill="none" stroke="#9aa0a8" stroke-width="2"/><line x1="11.5" y1="11.5" x2="16" y2="16" stroke="#9aa0a8" stroke-width="2.4"/></svg>
      Search...
    </div>
    <svg class="abs icon-btn" style="left:958px" width="42" height="42" viewBox="0 0 42 42" aria-label="Messages">
      <rect x="2" y="12" width="34" height="24" fill="#2e3b55"/>
      <polyline points="2,12 19,27 36,12" fill="none" stroke="#fff" stroke-width="2"/>
      <polyline points="2,36 14,23 M24,23" fill="none" stroke="#fff" stroke-width="2"/>
      <line x1="36" y1="36" x2="24" y2="23" stroke="#fff" stroke-width="2"/>
      <circle cx="34" cy="14" r="6" fill="#f0478f" stroke="#fff" stroke-width="2"/>
    </svg>
    <svg class="abs icon-btn" style="left:1024px" width="36" height="44" viewBox="0 0 36 44" aria-label="Notifications">
      <path d="M6 34 L30 34 L27 29 L27 18 Q27 9 18 8 Q9 9 9 18 L9 29 Z" fill="#2e3b55"/>
      <ellipse cx="18" cy="38" rx="4" ry="3" fill="#2e3b55"/>
      <circle cx="25" cy="10" r="6" fill="#f0478f" stroke="#fff" stroke-width="2"/>
    </svg>
    <div class="abs user">
      <div class="avatar-round" role="img" aria-label="Profile photo of Dana Whitford"></div>
      Dana Whitford
      <svg width="14" height="8" viewBox="0 0 14 8"><polygon points="0,0 14,0 7,8" fill="#3a4b66"/></svg>
    </div>
    <svg class="abs menu" width="30" height="22" viewBox="0 0 30 22"><rect y="0" width="30" height="3" fill="#2e3b55"/><rect y="9" width="30" height="3" fill="#2e3b55"/><rect y="18" width="30" height="3" fill="#2e3b55"/></svg>
  </header>

  <h1 class="abs page-title" style="font-weight:400">Dashboard</h1>
  <p class="abs page-sub">Welcome to Keystone</p>
  <span class="abs range-label">Date Range</span>
  <div class="abs range-box">
    <span>19-09-2020 &nbsp;- &nbsp;19-01 -2021</span>
    <svg width="22" height="22" viewBox="0 0 22 22"><rect x="1" y="3" width="20" height="18" fill="none" stroke="#555" stroke-width="1.6"/><line x1="1" y1="8" x2="21" y2="8" stroke="#555" stroke-width="1.6"/><line x1="6" y1="1" x2="6" y2="5" stroke="#555" stroke-width="1.6"/><line x1="16" y1="1" x2="16" y2="5" stroke="#555" stroke-width="1.6"/><g fill="#555"><rect x="4" y="11" width="2" height="2"/><rect x="8" y="11" width="2" height="2"/><rect x="12" y="11" width="2" height="2"/><rect x="16" y="11" width="2" height="2"/><rect x="4" y="15" width="2" height="2"/><rect x="8" y="15" width="2" height="2"/><rect x="12" y="15" width="2" height="2"/><rect x="16" y="15" width="2" height="2"/></g></svg>
  </div>

  <!-- stat cards -->
  <section class="abs stat c-props">
    <svg width="50" height="52" viewBox="0 0 50 52" fill="none" stroke="#fff" stroke-width="2"><rect x="6" y="8" width="22" height="42"/><rect x="28" y="22" width="16" height="28"/><line x1="2" y1="50" x2="48" y2="50"/><g fill="#fff" stroke="none"><rect x="10" y="14" width="4" height="4"/><rect x="19" y="14" width="4" height="4"/><rect x="10" y="24" width="4" height="4"/><rect x="19" y="24" width="4" height="4"/><rect x="10" y="34" width="4" height="4"/><rect x="19" y="34" width="4" height="4"/><rect x="32" y="28" width="3" height="3"/><rect x="38" y="28" width="3" height="3"/><rect x="32" y="36" width="3" height="3"/><rect x="38" y="36" width="3" height="3"/></g></svg>
    <div><div class="stat-label">PROPERTIES</div><div class="stat-value">03</div></div>
  </section>
  <section class="abs stat c-tenants">
    <svg width="50" height="56" viewBox="0 0 50 56" fill="none" stroke="#fff" stroke-width="2"><circle cx="28" cy="10" r="7"/><line x1="28" y1="17" x2="28" y2="36"/><line x1="28" y1="26" x2="33" y2="26"/><line x1="28" y1="31" x2="33" y2="31"/><path d="M2 44 L14 40 L30 42 Q34 44 30 46 L18 46 M2 52 L20 52 L46 42 Q48 38 44 38 L30 42"/></svg>
    <div><div class="stat-label">TENANTS</div><div class="stat-value">08</div></div>
  </section>
  <section class="abs stat c-area">
    <svg width="54" height="52" viewBox="0 0 54 52" fill="none" stroke="#fff" stroke-width="2"><rect x="24" y="4" width="24" height="46"/><path d="M4 50 L4 26 L16 16 L28 26"/><rect x="10" y="34" width="8" height="16"/><line x1="0" y1="50" x2="54" y2="50"/><g fill="#fff" stroke="none"><rect x="30" y="10" width="4" height="4"/><rect x="38" y="10" width="4" height="4"/><rect x="30" y="20" width="4" height="4"/><rect x="38" y="20" width="4" height="4"/><rect x="38" y="30" width="4" height="4"/><rect x="38" y="40" width="4" height="4"/></g></svg>
    <div><div class="stat-label">TOTAL PROPERTIES AREA</div><div class="stat-value">422,000.00sq.ft.</div></div>
  </section>
  <section class="abs stat c-rented">
    <svg width="58" height="54" viewBox="0 0 58 54" fill="none" stroke="#fff" stroke-width="2"><path d="M2 22 L29 3 L56 22"/><path d="M8 20 L8 50 L50 50 L50 20"/><circle cx="29" cy="15" r="4"/><rect x="14" y="24" width="30" height="14"/><text x="29" y="35" text-anchor="middle" font-family="Lato,sans-serif" font-size="10" fill="#fff" stroke="none">RENT</text><line x1="2" y1="50" x2="56" y2="50"/></svg>
    <div><div class="stat-label">RENTED AREA</div><div class="stat-value">233,500.00sq.ft.</div></div>
  </section>
  <section class="abs stat c-vacant">
    <svg width="50" height="52" viewBox="0 0 50 52" fill="none" stroke="#fff" stroke-width="2"><rect x="6" y="4" width="22" height="46"/><rect x="28" y="20" width="16" height="30"/><line x1="2" y1="50" x2="48" y2="50"/><g fill="#fff" stroke="none"><rect x="10" y="10" width="4" height="4"/><rect x="19" y="10" width="4" height="4"/><rect x="10" y="20" width="4" height="4"/><rect x="19" y="20" width="4" height="4"/><rect x="10" y="30" width="4" height="4"/><rect x="19" y="30" width="4" height="4"/><rect x="32" y="26" width="3" height="3"/><rect x="38" y="26" width="3" height="3"/><rect x="32" y="36" width="3" height="3"/><rect x="38" y="36" width="3" height="3"/></g></svg>
    <div><div class="stat-label">VACANCIES AREA</div><div class="stat-value">188,500.00sq.ft</div></div>
  </section>

  <!-- line chart -->
  <section class="abs chart-panel">
    <div class="abs filters">
      <label><span class="radio on"></span>Last 7 days</label>
      <label><span class="radio"></span>Last months</label>
      <label><span class="radio"></span>Last 7 months</label>
      <label><span class="radio"></span>Next 7 days</label>
      <label><span class="radio"></span>Next months</label>
      <label><span class="radio"></span>Next 3 months</label>
    </div>
    <svg class="abs" style="left:0;top:0" width="1344" height="591" viewBox="27 327 1344 591" font-family="Lato,sans-serif">
      <g stroke="var(--grid)" stroke-width="1">
        <line x1="85" y1="462" x2="1361" y2="462"/><line x1="85" y1="535" x2="1361" y2="535"/>
        <line x1="85" y1="608" x2="1361" y2="608"/><line x1="85" y1="681" x2="1361" y2="681"/>
        <line x1="85" y1="755" x2="1361" y2="755"/><line x1="85" y1="829" x2="1361" y2="829"/>
        <line x1="85" y1="424" x2="85" y2="829"/><line x1="244" y1="424" x2="244" y2="829"/>
        <line x1="404" y1="424" x2="404" y2="829"/><line x1="563" y1="424" x2="563" y2="829"/>
        <line x1="723" y1="424" x2="723" y2="829"/><line x1="882" y1="424" x2="882" y2="829"/>
        <line x1="1041" y1="424" x2="1041" y2="829"/><line x1="1201" y1="424" x2="1201" y2="829"/>
        <line x1="1361" y1="424" x2="1361" y2="829"/>
      </g>
      <g font-size="18" fill="#333" text-anchor="end">
        <text x="80" y="469">1.25</text><text x="80" y="542">1</text><text x="80" y="615">0.75</text>
        <text x="80" y="688">0.5</text><text x="80" y="761">0.25</text><text x="80" y="833">0</text>
      </g>
      <g font-size="17" fill="#333" text-anchor="middle">
        <text x="250" y="850">27Dec</text><text x="245" y="871">2020</text>
        <text x="412" y="850">28Dec</text><text x="407" y="871">2020</text>
        <text x="567" y="850">29Dec</text><text x="562" y="871">2020</text>
        <text x="729" y="850">30Dec</text><text x="724" y="871">2020</text>
        <text x="887" y="850">31Dec</text><text x="882" y="871">2020</text>
        <text x="1048" y="850">01Jan</text><text x="1044" y="871">2021</text>
        <text x="1212" y="850">02Jan</text><text x="1208" y="871">2021</text>
      </g>
      <path d="M90 826 C120 812 150 803 175 803 C205 803 235 760 284 755 C330 748 370 720 405 721 C430 722 450 700 471 683 C500 655 530 612 564 609 C610 604 660 535 725 535 C760 540 780 546 810 545 C850 544 870 530 900 522 C960 500 1020 480 1060 470 C1100 462 1120 455 1147 451" fill="none" stroke="var(--line)" stroke-width="2.5"/>
      <g fill="var(--line)">
        <circle cx="90" cy="826" r="6.5"/><circle cx="284" cy="755" r="6.5"/><circle cx="405" cy="721" r="6.5"/>
        <circle cx="471" cy="683" r="6.5"/><circle cx="564" cy="609" r="6.5"/><circle cx="725" cy="535" r="6.5"/>
      </g>
    </svg>
  </section>

  <!-- work order donut -->
  <section class="abs donut-panel">
    <svg class="abs" style="left:30px;top:60px" width="280" height="280" viewBox="0 0 280 280">
      <g transform="rotate(-90 140 140)" fill="none" stroke-width="27">
        <circle cx="140" cy="140" r="122" pathLength="360" stroke="#3c3d45" stroke-dasharray="86 360" stroke-dashoffset="46"/>
        <circle cx="140" cy="140" r="122" pathLength="360" stroke="#f6a25a" stroke-dasharray="82 360" stroke-dashoffset="-40"/>
        <circle cx="140" cy="140" r="122" pathLength="360" stroke="#e5d650" stroke-dasharray="45 360" stroke-dashoffset="-122"/>
        <circle cx="140" cy="140" r="122" pathLength="360" stroke="#8ae87b" stroke-dasharray="30 360" stroke-dashoffset="-167"/>
        <circle cx="140" cy="140" r="122" pathLength="360" stroke="#ef5b80" stroke-dasharray="41 360" stroke-dashoffset="-197"/>
        <circle cx="140" cy="140" r="122" pathLength="360" stroke="#7bb5ef" stroke-dasharray="47 360" stroke-dashoffset="-238"/>
        <circle cx="140" cy="140" r="122" pathLength="360" stroke="#7f7ef0" stroke-dasharray="29 360" stroke-dashoffset="-285"/>
      </g>
    </svg>
    <ul class="abs legend">
      <li><span class="dot" style="background:#7bb5ef"></span>Scheduled Maintenance</li>
      <li><span class="dot" style="background:#8ae87b"></span>Completed Scheduled Maintenance</li>
      <li><span class="dot" style="background:#f6a25a"></span>Future Scheduled Maintenance</li>
      <li><span class="dot" style="background:#3c3d45"></span>Scheduled Work Orders</li>
      <li><span class="dot" style="background:#7f7ef0"></span>Completed Work Orders</li>
      <li><span class="dot" style="background:#ef5b80"></span>Property Inpections In Progress</li>
      <li><span class="dot" style="background:#e5d650"></span>Completed Property Inpections</li>
    </ul>
  </section>

  <!-- users -->
  <h2 class="abs users-title" style="font-weight:400">Users</h2>
  <span class="abs users-range">last 24 hours</span>
  <section class="abs users-panel">
    <div class="abs user-row" style="top:26px">
      <div class="photo" role="img" aria-label="User portrait" style="background:linear-gradient(135deg,#d9cfc6,#8a6a55)"></div>
      <div class="user-info"><div class="user-name">Marco Ellis</div><div class="user-role">Lorem Ipsum</div></div>
      <div class="status">Online</div>
    </div>
    <div class="abs user-row" style="top:124px">
      <div class="photo" role="img" aria-label="User portrait" style="background:linear-gradient(135deg,#2a3a4c,#9aa9b8)"></div>
      <div class="user-info"><div class="user-name">Marco Ellis</div><div class="user-role">Lorem Ipsum</div></div>
      <div class="status">Online</div>
    </div>
    <div class="abs user-row" style="top:222px">
      <div class="photo" role="img" aria-label="User portrait" style="background:linear-gradient(135deg,#c9d3c0,#8a6b57)"></div>
      <div class="user-info"><div class="user-name">Marco Ellis</div><div class="user-role">Lorem Ipsum</div></div>
      <div class="status">Online</div>
    </div>
    <div class="abs user-row" style="top:320px">
      <div class="photo" role="img" aria-label="User portrait" style="background:linear-gradient(135deg,#e3e4e6,#6e7d8c)"></div>
      <div class="user-info"><div class="user-name">Marco Ellis</div><div class="user-role">Lorem Ipsum</div></div>
      <div class="status">Online</div>
    </div>
  </section>

</div>
</body>
</html>
```